Flowy subpage design wanted for a modern tax/accounting firm in Switzerland

--- Introduction ---
We are a tax and accounting firm in Switzerland. We provide services for expats living in Switzerland, our service is quite exclusive and modern (digital).

We just relaunched our website www.fiscavantra.ch and are happy with the design, so the desired subpage (more details below) should of course fit in.

--- Main brief ---
Please see Word File attached. The page has to include the whole text (11 chapters). A very intuitive, flowy design on only one subpage (not one page per chapter) is a MUST. Also, it is key that the design is supporting the content of the individual chapters, so it would be advantageous if you'd have a good unterstanding of the text attached.

--- Further information ---
A similar example would be this one: https://www2.brennick.com/ch/en/pages/tax/articles/living-working-switzerland.html

This one is similar in what concerns the content, but NOT what we are looking for designwise. It is very simple and looks "thrown together", just not aesthetically pleasing in our opinion.

--- Final thoughts ---
- If you blow our minds with your design, we will certainly have future work for you.
- Our clients are between 20-50 years old, well educated, high income / high wealth, English speaking and living in Switzerland.
- CI/CD information:
Fonts
Montserrat regular / medium italic / bold
Colors
White #ffffffff
Darkblue #0a2b46
Darkblue 25% #b5bfc8
Darkblue 50% #8595a4
Greenblue #0d4261

We are looking forward to your designs!
Updates

Thank you very much for the submitted designs and your efforts. Unfortunately, none of the designs meet our expectations so far. Please note the following: - Designs that do not take CI into account will not be looked at more closely. - We have received many simple designs with very simple structure and accordion elements. But more important than the simple structure is an eye-catching design! Make it flowy and beautiful - We don't want pictures of Swiss vehicles, passes or other pictures that don't actively support the text. If you can make an illustration that really fits the context, fine, otherwise better leave it without. Thank you

Target Market(s)

Expats living in Switzerland. High income earners / high net worth individuals

Industry/Entity Type

tax/accounting

Number of Pages Required

1 page

Font styles to use
Other font styles liked:
• Montserrat

Colors
0054AA
0677BA
7BADD7
CADEEF
E8F1F8

Requirements
Must have
• based on general website design
Nice to have
• intuitive, flowy, attractive representation of much text
Should not have
• basic copy/paste of the text in sections :)

```html
<!DOCTYPE html>
<html lang="en">
<head>
<meta charset="utf-8">
<title>Living &amp; Working in Switzerland – Fiscavantra Advisory</title>
<link href="https://fonts.googleapis.com/css2?family=Montserrat:ital,wght@0,400;0,500;0,600;0,700;1,500&display=swap" rel="stylesheet">
<style>
:root{
  --navy:#0a2b46;
  --greenblue:#0d4261;
  --navy-50:#8595a4;
  --navy-25:#b5bfc8;
  --bar:#e6eaee;
  --stage:#eceef0;
  --white:#ffffff;
  --text:#4a5a68;
  --link:#0054aa;
}
*{box-sizing:border-box;margin:0;padding:0}
html,body{width:1200px;height:3458px;overflow:hidden}
body{background:var(--stage);font-family:'Montserrat',sans-serif;color:var(--text);position:relative}
.page{position:absolute;left:201px;top:29px;width:798px;height:3400px;background:var(--white);overflow:hidden;box-shadow:0 4px 30px rgba(10,43,70,.08)}
.abs{position:absolute}

/* nav */
.site-nav{left:0;top:0;width:798px;height:48px;display:flex;align-items:center;padding:0 72px 0 108px;border-bottom:1px solid #eef1f3}
.brand{display:flex;align-items:center;gap:7px;color:var(--navy);font-weight:600;line-height:1.05}
.brand-dot{width:26px;height:26px;border-radius:50%;background:var(--navy)}
.brand-name{font-size:11px;letter-spacing:.06em}
.nav-links{margin-left:auto;display:flex;gap:16px;font-size:7.5px;color:var(--navy-50)}
.nav-links .active{color:var(--navy);font-weight:600;border-bottom:2px solid var(--navy);padding-bottom:14px;margin-bottom:-17px}
.btn-calc{margin-left:24px;background:var(--navy);color:#fff;font-size:7.5px;padding:6px 10px;display:flex;align-items:center;gap:5px}
.btn-calc i{width:7px;height:8px;border:1px solid #fff;display:block}

/* hero */
.hero{left:0;top:48px;width:798px;height:272px;background:linear-gradient(100deg,#bccbe0 0%,#dbe3ee 45%,#edf1f5 100%)}
.hero-photo{left:430px;top:48px;width:368px;height:230px;background:linear-gradient(160deg,#e9eef4 0%,#b6c3d3 55%,#7d8ea3 100%);opacity:.85}
.hero-shape{left:0;top:48px}
.hero-title{left:108px;top:124px;font-size:24px;line-height:1.2;color:var(--navy);font-weight:400}
.hero-title b{font-weight:600}

/* tabs */
.tabs{left:108px;top:360px;width:584px;display:grid;grid-template-columns:repeat(5,1fr);row-gap:22px;font-size:6.8px;color:var(--navy-50)}
.tabs span{padding:0 0 6px 12px;border-bottom:1px solid transparent}
.tabs .current{color:var(--navy);border-bottom:1px solid var(--navy)}

.chapter-title{left:0;width:798px;top:502px;text-align:center;font-size:19px;font-weight:400;color:var(--navy)}
.chapter-title b{font-weight:600}
.chapter-lead{left:199px;width:400px;top:540px;text-align:center;font-size:7.2px;line-height:1.9}

/* sections */
.photo{background:#9aa9b8}
.framed::before{content:"";position:absolute;top:-6px;left:-6px;right:6px;bottom:6px;border-top:1px solid var(--navy);border-left:1px solid var(--navy)}
.framed.right::before{left:6px;right:-6px;border-left:none;border-right:1px solid var(--navy)}
.block{width:278px;font-size:6.8px;line-height:2.05}
.block h2{font-size:12.5px;font-weight:400;color:var(--greenblue);margin-bottom:9px;line-height:1.3}
.block h2 b{font-weight:600}
.block p{margin-bottom:3px}
.block ul{margin:0 0 3px 8px;color:var(--link)}
.block a{color:var(--link)}
.acc{background:var(--bar);height:24px;display:flex;align-items:center;justify-content:space-between;padding:0 10px;font-size:7px;color:var(--navy-50);margin-bottom:10px;line-height:1}
.acc svg{width:8px;height:5px}
.acc.open{background:var(--navy);color:#fff;margin-bottom:0}
.acc-body{padding:7px 10px 8px;margin-bottom:10px}

/* footer */
.site-footer{left:0;top:3177px;width:798px;height:223px;background:var(--navy);color:#c8d1da}
.foot-col{position:absolute;top:38px;font-size:6.5px;line-height:1.85}
.foot-col h3{font-size:7px;font-weight:700;color:#fff;margin-bottom:14px}
.foot-brand{color:#fff}
.foot-contact{margin-top:16px}
.foot-contact div{display:flex;align-items:center;gap:5px;color:#fff}
.foot-contact svg{width:7px;height:7px}
.foot-bottom{position:absolute;left:0;bottom:0;width:798px;height:32px;border-top:1px solid rgba(255,255,255,.15);text-align:center;font-size:6px;line-height:32px;color:#9fb0c0}
</style>
</head>
<body>
<div class="page">

  <header class="site-nav abs">
    <div class="brand"><span class="brand-dot"></span><span class="brand-name">FISCAVANTRA<br>ADVISORY</span></div>
    <nav class="nav-links"><span>Home</span><span>Tax returns</span><span class="active">More services ▾</span><span>Swiss tax guide</span><span>About us</span></nav>
    <div class="btn-calc"><i></i>Calculate</div>
  </header>

  <div class="hero abs"></div>
  <div class="hero-photo abs" role="img" aria-label="Glass office tower seen from below against a pale sky"></div>
  <svg class="hero-shape abs" width="798" height="300" viewBox="0 0 798 300">
    <polygon points="0,240 798,274 798,300 0,300" fill="#ffffff"/>
    <polygon points="415,257 798,156 798,274" fill="#0a2b46"/>
  </svg>
  <h1 class="hero-title abs">Living &amp; Working<br><b>in Switzerland</b></h1>

  <nav class="tabs abs">
    <span class="current">1. Life in Switzerland</span><span>2. CH - A brief overview</span><span>3. Immigration to CH</span><span>4. Labor law in CH</span><span>5. Double taxation</span>
    <span>6. Indirect taxes in CH</span><span>7. Other federal Taxes</span><span>8. Rent &amp; buy in CH</span><span>9. Childcare in CH</span><span>10. Public transportation</span>
    <span>11. Recreation</span>
  </nav>

  <h2 class="chapter-title abs">1.Life <b>in Switzerland</b></h2>
  <p class="chapter-lead abs">To give you a small impression of what to expect when living in Switzerland, we have put together some topics for you to make your new start in Switzerland as pleasant as possible.</p>

  <!-- General -->
  <div class="photo framed abs" style="left:108px;top:604px;width:278px;height:392px;background:linear-gradient(180deg,#5c6f80,#8a9aa6 50%,#4d6070)" role="img" aria-label="Aerial view of people walking across a city bridge over a river"></div>
  <div class="block abs" style="left:414px;top:606px">
    <h2>General</h2>
    <div class="acc">4 official languages<svg viewBox="0 0 8 5"><path d="M1 1l3 3 3-3" fill="none" stroke="currentColor"/></svg></div>
    <div class="acc open">Currency and banking<svg viewBox="0 0 8 5"><path d="M1 4l3-3 3 3" fill="none" stroke="currentColor"/></svg></div>
    <div class="acc-body">
      <p>The national currency in Switzerland is the Swiss franc (CHF). 1 Swiss franc (Franken) is equal to 100 centimes (Rappen).</p>
      <p>The banknotes are available in the following amounts: 10, 20, 50, 100, 200</p>
      <p>For coins, there are the following denominations:</p>
      <ul><li>CHF 1, 2, 5</li><li>5, 10, 20, 50 centimes</li></ul>
      <p>Current accounts can be opened at any major bank, postal banks, cantonal or private banks. The largest banks in Switzerland are Lemanbank, Tessera Bank and Brügg Finanz.</p>
    </div>
    <div class="acc">Public holidays<svg viewBox="0 0 8 5"><path d="M1 1l3 3 3-3" fill="none" stroke="currentColor"/></svg></div>
    <div class="acc">Usual business and store opening hours<svg viewBox="0 0 8 5"><path d="M1 1l3 3 3-3" fill="none" stroke="currentColor"/></svg></div>
    <div class="acc">Electricity and water<svg viewBox="0 0 8 5"><path d="M1 1l3 3 3-3" fill="none" stroke="currentColor"/></svg></div>
    <div class="acc">Telephone and television<svg viewBox="0 0 8 5"><path d="M1 1l3 3 3-3" fill="none" stroke="currentColor"/></svg></div>
  </div>

  <!-- Living -->
  <div class="block abs" style="left:108px;top:1077px">
    <h2>Living <b>in Switzerland</b></h2>
    <div class="acc">Rent<svg viewBox="0 0 8 5"><path d="M1 1l3 3 3-3" fill="none" stroke="currentColor"/></svg></div>
    <div class="acc open">Buy<svg viewBox="0 0 8 5"><path d="M1 4l3-3 3 3" fill="none" stroke="currentColor"/></svg></div>
    <div class="acc-body">
      <p>Under certain conditions, it is also possible for non-Swiss nationals to purchase residential property in Switzerland.</p>
      <p>A down payment of 20% of the purchase price must be made from equity, as a maximum mortgage of 80% of the purchase price can be taken out.</p>
      <p>The purchase of a property changes the tax situation of the buyer, as the residential property is henceforth included in the assets and is therefore subject to wealth tax (which varies from canton to canton). It is advisable to consult with a tax expert before purchasing a property.</p>
    </div>
  </div>
  <div class="photo framed right abs" style="left:414px;top:1074px;width:278px;height:256px;background:linear-gradient(180deg,#d7e2ea 0%,#b79f86 45%,#3f6a86 70%,#2c4f68)" role="img" aria-label="Old town waterfront with church towers beside a lake"></div>

  <!-- Education -->
  <div class="photo framed abs" style="left:108px;top:1405px;width:278px;height:405px;background:linear-gradient(180deg,#e4eaf0 0%,#c3cfdb 45%,#5b6f82 80%,#3a4d60)" role="img" aria-label="Audience seated in a lecture hall facing a presenter"></div>
  <div class="block abs" style="left:414px;top:1403px">
    <h2>The education <b>system in Switzerland</b></h2>
    <p>In Switzerland, there are both public and private schools. The public schools are financed by the cantons and attendance at such a school is free of charge.</p>
    <p>Compulsory kindergarten or schooling begins at the age of 4. A minimum of 11 years of schooling is compulsory.</p>
    <p>Public educational institutions are classified as follows:</p>
    <ul><li>Kindergarten: age 4-6 years, compulsory in most cantons</li><li>Elementary school: ages 6-12, grades 1-6, mandatory</li><li>Secondary school: age 12-15, compulsory, leads to completion of compulsory education plan</li><li>After secondary school: special schools for preparation for higher education (e.g. university) or training centers for trainees</li></ul>
    <p>Anyone wishing to enroll their child in the Swiss public school system must contact the cantonal education authority and provide the following proof:</p>
    <ul><li>Valid residence permit for Switzerland</li><li>Health and accident insurance for the child</li></ul>
    <p>If a foreign child is between the ages of 12 and 15, he or she must pass an entrance exam before enrolling in a public school, which tests, among other things, sufficient proficiency in the language of instruction.</p>
    <p>Enrolling the child in a private school is also possible. However, depending on the school, waiting times for a free place can be several years.</p>
  </div>

  <!-- Healthcare -->
  <div class="block abs" style="left:108px;top:1896px">
    <h2>The healthcare <b>system in Switzerland</b></h2>
    <p>The healthcare system in Switzerland is one of the best in the world. Even in less densely populated regions, the density of hospitals and doctors' offices is high, so that medical care is always timely.</p>
    <p>The federal government sets the financial framework within which health insurers may offer their premiums. It must also give its prior consent to premium increases and can also reject them.</p>
    <p>The cantons and municipalities are responsible for regulating hospitals. This means that it is determined at the cantonal level which hospital provides which services and how high the wages of doctors and nursing staff are.</p>
    <p>Compulsory health insurance applies in Switzerland. Everyone who lives here must have health insurance. The insurers are private companies, but may only operate within the legal framework set by the federal government.</p>
    <p>The companies are obliged to include every citizen in the so-called basic insurance – without a prior health check. Insured persons can add further services to their plan at an additional cost, if they wish.</p>
    <p><a>Every citizen is free to choose an insurer.</a> The monthly premiums differ in part very much from insurer to insurer. Therefore, it is advisable to compare benefits and premiums beforehand.</p>
  </div>
  <div class="photo framed right abs" style="left:414px;top:1886px;width:278px;height:400px;background:linear-gradient(170deg,#dde4ea 0%,#9fb0c0 50%,#5e7186)" role="img" aria-label="Doctors in white coats talking on a hospital staircase"></div>

  <!-- Driving -->
  <div class="photo framed abs" style="left:108px;top:2362px;width:278px;height:442px;background:linear-gradient(180deg,#c9d3df 0%,#d9c4c2 28%,#6d7e8e 60%,#3f4d5b)" role="img" aria-label="Busy motorway with traffic at dusk"></div>
  <div class="block abs" style="left:414px;top:2361px">
    <h2>Driving <b>in Switzerland</b></h2>
    <div class="acc">General information about driving in Switzerland<svg viewBox="0 0 8 5"><path d="M1 1l3 3 3-3" fill="none" stroke="currentColor"/></svg></div>
    <div class="acc open">Currency and banking<svg viewBox="0 0 8 5"><path d="M1 4l3-3 3 3" fill="none" stroke="currentColor"/></svg></div>
    <div class="acc-body">
      <p>A valid driver's license is required to drive a vehicle. Foreigners may drive in Switzerland for up to one year with a license from their home country or an international driver's license. After that, a Swiss license must be applied for at the traffic licensing authority. Necessary for this are:</p>
      <ul><li>Completing the application to exchange the foreign license for a Swiss driver's license</li><li>Enclose the previous license (it is then stamped "invalid in Switzerland")</li><li>Proof of a vision test by an ophthalmologist</li><li>Passport photo</li><li>Foreigner's identity card (B or C) as confirmation</li></ul>
    </div>
    <div class="acc">Have vehicle safety checked<svg viewBox="0 0 8 5"><path d="M1 1l3 3 3-3" fill="none" stroke="currentColor"/></svg></div>
    <div class="acc">Buy vehicle<svg viewBox="0 0 8 5"><path d="M1 1l3 3 3-3" fill="none" stroke="currentColor"/></svg></div>
    <div class="acc">Import vehicle<svg viewBox="0 0 8 5"><path d="M1 1l3 3 3-3" fill="none" stroke="currentColor"/></svg></div>
    <div class="acc">Insure vehicle<svg viewBox="0 0 8 5"><path d="M1 1l3 3 3-3" fill="none" stroke="currentColor"/></svg></div>
  </div>

  <!-- Public transport -->
  <div class="block abs" style="left:108px;top:2880px">
    <h2>Public transport <b>in Switzerland</b></h2>
    <div class="acc">Bus and train<svg viewBox="0 0 8 5"><path d="M1 1l3 3 3-3" fill="none" stroke="currentColor"/></svg></div>
    <div class="acc open">Air traffic<svg viewBox="0 0 8 5"><path d="M1 4l3-3 3 3" fill="none" stroke="currentColor"/></svg></div>
    <div class="acc-body">
      <p>Internationally, Switzerland is easy to reach from any corner of the world with three national airports, located in <a>Zurich, Geneva and Basel-Mulhouse</a> (which lies in France near the Swiss border).</p>
      <p>In addition, eleven regional airports serve various destinations in Europe.</p>
      <p>From Zurich and Geneva, destinations within and outside Europe are served, and from Basel-Mulhouse, destinations within Europe.</p>
    </div>
  </div>
  <div class="photo framed right abs" style="left:408px;top:2880px;width:284px;height:236px;background:linear-gradient(180deg,#3b5f8d 0%,#6f8fb6 40%,#2b3f58 100%)" role="img" aria-label="Airport terminal facade with an airliner overhead"></div>

  <!-- Footer -->
  <footer class="site-footer abs">
    <div class="foot-col" style="left:108px">
      <div class="brand foot-brand"><span class="brand-dot" style="background:#fff"></span><span class="brand-name">FISCAVANTRA<br>ADVISORY</span></div>
      <div class="foot-contact">
        <div><svg viewBox="0 0 8 8"><path d="M4 0a3 3 0 0 0-3 3c0 2 3 5 3 5s3-3 3-5a3 3 0 0 0-3-3z" fill="#fff"/></svg>Office Zug | Lindenweg 12</div>
        <div><svg viewBox="0 0 8 8"><path d="M1 1l2 0 1 2-1 1a5 5 0 0 0 1 1l1-1 2 1v2C3 7 1 5 1 1z" fill="#fff"/></svg>Available for existing clients only</div>
        <div><svg viewBox="0 0 8 8"><rect x="0.5" y="1.5" width="7" height="5" fill="none" stroke="#fff"/><path d="M.5 1.5l3.5 3 3.5-3" fill="none" stroke="#fff"/></svg>Available for existing clients only</div>
      </div>
    </div>
    <div class="foot-col" style="left:306px;width:170px">
      <h3>ABOUT FISCAVANTRA</h3>
      <p>Fiscavantra Advisory was founded in 2014 with the vision to make Swiss tax matters uncomplicated and painless for expats without compromising quality or making the service unaffordable.</p>
    </div>
    <div class="foot-col" style="left:558px">
      <h3>QUICK LINKS</h3>
      <p>Tax returns<br>All-in-one<br>Swiss tax guide<br>About us<br>Privacy policy</p>
    </div>
    <div class="foot-bottom">© 2022 Fiscavantra Advisory LLC All Right Reserved | Privacy Policy | Impressum</div>
  </footer>

</div>
</body>
</html>
```